Christmas Collection Candle Label Design

Looking to update our existing Christmas Candle Collection labels. Labels should reflect the overall feel of our brand- www.kelvanoro.ca
Want to include some color elements. Holiday colors added into design but more muted/ earthy tones not vibrant colors . Metallic elements and line art botanical illustration. Fonts should be more align to brand
Scents
Holiday Tree
Candy Cane
Sugar and Spice
Joyeaux Noel

```html
<!DOCTYPE html>
<html lang="en">
<head>
<meta charset="utf-8">
<title>Joyeaux Noel – Candle Label</title>
<link href="https://fonts.googleapis.com/css2?family=Libre+Baskerville:wght@700&family=Open+Sans:wght@400;600&display=swap" rel="stylesheet">
<style>
  :root {
    --backdrop: #c9cbca;
    --sage-light: #7d8f87;
    --sage-dark: #5e6d66;
    --cream: #e8dccf;
    --botanical: #9aa58f;
  }
  * { margin: 0; padding: 0; box-sizing: border-box; }
  html, body { width: 1200px; height: 749px; overflow: hidden; }
  body {
    background: var(--backdrop);
    font-family: "Open Sans", sans-serif;
    position: relative;
  }
  .label {
    position: absolute;
    left: 390px;
    top: 205px;
    width: 420px;
    height: 330px;
    background: linear-gradient(90deg, var(--sage-light) 0%, #6d7f77 45%, var(--sage-dark) 100%);
    color: var(--cream);
  }
  .brand {
    position: absolute;
    top: 38px;
    left: 0;
    width: 100%;
    text-align: center;
  }
  .brand-name {
    font-size: 15px;
    font-weight: 400;
    letter-spacing: 0.5px;
    line-height: 1;
  }
  .brand-tagline {
    margin-top: 3px;
    font-size: 4.5px;
    letter-spacing: 1.2px;
  }
  .rule {
    position: absolute;
    left: 27px;
    width: 355px;
    height: 1.5px;
    background: var(--cream);
  }
  .rule-top { top: 79px; }
  .rule-bottom-a { top: 255px; }
  .rule-bottom-b { top: 302px; }
  .scent-name {
    position: absolute;
    left: 27px;
    top: 100px;
    font-family: "Libre Baskerville", serif;
    font-weight: 700;
    font-size: 44px;
    line-height: 1.1;
    letter-spacing: 0.5px;
  }
  .scent-note {
    position: absolute;
    left: 29px;
    top: 215px;
    font-size: 9.5px;
    font-weight: 600;
  }
  .botanical {
    position: absolute;
    left: 268px;
    top: 92px;
    width: 148px;
    height: 158px;
    border-radius: 40% 45% 30% 50%;
    background: radial-gradient(circle at 55% 45%, rgba(154,165,143,0.45), rgba(154,165,143,0.08) 70%, transparent 100%);
  }
  .size, .origin, .divider {
    position: absolute;
    font-size: 9.5px;
    font-weight: 600;
  }
  .size { left: 29px; top: 268px; }
  .divider { left: 200px; top: 283px; font-weight: 400; }
  .origin { right: 38px; top: 280px; }
</style>
</head>
<body>
  <section class="label">
    <div class="brand">
      <div class="brand-name">KELVANORO</div>
      <div class="brand-tagline">PURE PLANT BASED SCENTS</div>
    </div>
    <div class="rule rule-top"></div>
    <h1 class="scent-name">JOYEAUX<br>NOEL</h1>
    <p class="scent-note">MADE WITH PLANT BASED BOTANICAL</p>
    <div class="botanical" role="img" aria-label="Line art illustration of lily flowers"></div>
    <div class="rule rule-bottom-a"></div>
    <span class="size">13 OZ</span>
    <span class="divider">//</span>
    <span class="origin">MADE IN CANADA</span>
    <div class="rule rule-bottom-b"></div>
  </section>
</body>
</html>
```